Corvane Freight Company Business Card Design

We are a company that delivers natural saltwater (from the ocean) to aquarium companies, restaurants and home marine tanks. I would like a new business card to suit.

Must include Name, company name, abn, contact number and website as well as logo (see attached).

Looking for a design that stands out, has a clean but unique appearance.

Double and single sided entries welcome

Business

• Logo

```html
<!DOCTYPE html>
<html lang="en">
<head>
<meta charset="utf-8">
<title>Corvane Freight Company – Business Card</title>
<link rel="stylesheet" href="https://fonts.googleapis.com/css2?family=Source+Sans+3:wght@400;600;700&display=swap">
<style>
  :root {
    --backdrop: #161616;
    --card-blue: #055bab;
    --accent-blue: #2aa6df;
    --card-white: #ffffff;
    --card-edge: #b9c8d8;
    --text-light: #ffffff;
  }
  * { box-sizing: border-box; margin: 0; padding: 0; }
  html, body {
    width: 1200px; height: 420px; overflow: hidden;
    background: var(--backdrop);
    font-family: "Source Sans 3", Arial, sans-serif;
  }
  .stage { position: relative; width: 1200px; height: 420px; }
  .card {
    position: absolute; top: 65px; width: 517px; height: 295px;
    border-radius: 28px; overflow: hidden;
  }
  .card-front { left: 69px; background: var(--card-white); display: flex; }
  .card-back {
    left: 621px; background: var(--card-blue);
    border: 1px solid var(--card-edge);
    display: flex; align-items: center; justify-content: center;
  }
  .brand-panel {
    width: 271px; height: 100%;
    display: flex; align-items: center; justify-content: center;
    padding: 0 18px;
  }
  .brand-name {
    font-weight: 600; color: var(--accent-blue);
    font-size: 25px; line-height: 1.1; text-align: center;
  }
  .divider { width: 3px; background: var(--accent-blue); margin-left: 2px; }
  .divider-gap { width: 3px; background: var(--card-white); }
  .details-panel {
    flex: 1; background: var(--card-blue); color: var(--text-light);
    padding: 58px 0 0 29px; font-size: 13px; line-height: 1.45;
  }
  .person-name { font-size: 18px; font-weight: 700; line-height: 1.2; }
  .person-title { font-size: 14px; margin-bottom: 20px; }
  .contact-line { display: flex; align-items: center; gap: 7px; }
  .contact-line svg { width: 11px; height: 11px; flex: none; }
  .address { margin-top: 16px; }
  .abn { margin-top: 18px; }
  .back-brand {
    font-weight: 600; color: var(--text-light);
    font-size: 50px; line-height: 1.05; text-align: center;
  }
</style>
</head>
<body>
<main class="stage">
  <section class="card card-front" aria-label="Card front">
    <div class="brand-panel">
      <p class="brand-name">Corvane Freight Company</p>
    </div>
    <div class="divider-gap"></div>
    <div class="divider"></div>
    <div class="details-panel">
      <p class="person-name">Your Name</p>
      <p class="person-title">Title</p>
      <p class="contact-line">
        <svg viewBox="0 0 12 12" aria-hidden="true"><path d="M2.5 1 L4.5 1 L5 3.5 L3.8 4.5 Q5 7 7.5 8.2 L8.5 7 L11 7.5 L11 9.5 Q10 11 8.5 11 Q1 9.5 1 3 Q1 1.5 2.5 1 Z" fill="none" stroke="currentColor" stroke-width="1"/></svg>
        123-456-7892
      </p>
      <p class="contact-line">
        <svg viewBox="0 0 12 12" aria-hidden="true"><circle cx="6" cy="6" r="5" fill="none" stroke="currentColor" stroke-width="1"/><ellipse cx="6" cy="6" rx="2.2" ry="5" fill="none" stroke="currentColor" stroke-width="0.9"/><line x1="1" y1="6" x2="11" y2="6" stroke="currentColor" stroke-width="0.9"/></svg>
        www.corvanefreight.com
      </p>
      <p class="address">Street Name, City Name ,<br>State, Zip Code</p>
      <p class="abn">ABN: 123456789</p>
    </div>
  </section>
  <section class="card card-back" aria-label="Card back">
    <p class="back-brand">Corvane Freight<br>Company</p>
  </section>
</main>
</body>
</html>
```